Junk Removal business needs a small billboard design

We are looking to have a billboard design made that will pop out to motorist passing by. The sign will be 6 foot wide by 4 foot tall. We would like it to say:SHOW US YOUR JUNK! 555-271-0836 BIG OR SMALL... WE HAUL IT ALL VICTORY JUNK REMOVALWe have provided a rough draft sketch photo of how large we would want the text. Preferably we want the text to be very large and use up most of the space and to be seen from far away. Also, there are example photos of the green background color and text colors we would like to incorporate into the design. We would like to add our company logo (Files attached) on the billboard too. Next to the phone number we would like to add the camera icon (example photos attached) Thank you in advance for all your hard work!

Font styles to use
Serif
Sans Serif

Requirements
Must have
• Large font that is easy to read from far
• Company name must be large
Nice to have
• Bright and pop out to passing by motorist.

```html
<!DOCTYPE html>
<html lang="en">
<head>
<meta charset="utf-8">
<title>Meadowlark Junk Removal – Billboard</title>
<link rel="stylesheet" href="https://fonts.googleapis.com/css2?family=Montserrat:wght@700;800;900&display=swap">
<style>
  :root {
    --backdrop: #a9a9a9;
    --grass: #8cbb47;
    --ink: #0a0a0a;
    --paper: #ffffff;
    --flame: #e2542f;
    --camera-body: #c4572b;
    --camera-top: #e8e8e8;
    --lens: #5d6468;
  }
  * { margin: 0; padding: 0; box-sizing: border-box; }
  html, body { width: 1200px; height: 1000px; overflow: hidden; }
  body {
    background: var(--backdrop);
    font-family: "Montserrat", Arial, sans-serif;
    position: relative;
  }
  .billboard {
    position: absolute;
    left: 83px; top: 155px;
    width: 1034px; height: 688px;
    background: var(--grass);
    overflow: hidden;
  }
  .footer-band {
    position: absolute;
    left: 0; top: 487px;
    width: 100%; height: 201px;
    background: var(--ink);
  }
  .headline-lead {
    position: absolute;
    left: 0; top: 20px; width: 100%;
    text-align: center;
    color: var(--paper);
    font-weight: 800;
    font-size: 84px;
    letter-spacing: -1px;
    line-height: 1;
  }
  .headline-main {
    position: absolute;
    left: 0; top: 0; width: 100%; height: 100%;
    font-size: 0;
  }
  .headline-word,
  .headline-bang {
    position: absolute;
    color: var(--paper);
    font-weight: 900;
    font-size: 296px;
    line-height: 1;
    -webkit-text-stroke: 14px var(--ink);
    paint-order: stroke fill;
    white-space: nowrap;
  }
  .headline-word {
    left: 37px; top: 82px;
    letter-spacing: -6px;
    transform: scaleX(0.93);
    transform-origin: left top;
  }
  .headline-bang {
    left: 916px; top: 82px;
  }
  .contact {
    position: absolute;
    left: 80px; top: 350px;
    display: flex; align-items: center; gap: 34px;
  }
  .camera-icon { width: 114px; height: 86px; display: block; }
  .phone {
    color: var(--ink);
    font-weight: 800;
    font-size: 108px;
    letter-spacing: -1px;
    line-height: 1;
    white-space: nowrap;
  }
  .ribbon {
    position: absolute;
    left: 45px; top: 455px;
    width: 944px; height: 68px;
  }
  .ribbon svg { position: absolute; inset: 0; width: 100%; height: 100%; }
  .ribbon-text {
    position: absolute; inset: 0;
    display: flex; align-items: center; justify-content: center;
    color: var(--paper);
    font-weight: 800;
    font-size: 49px;
    white-space: nowrap;
  }
  .brand {
    position: absolute;
    left: 92px; top: 540px;
    display: flex; align-items: center; gap: 86px;
  }
  .brand-mark {
    width: 120px; height: 120px;
    border-radius: 50%;
    background: #7d8564;
  }
  .brand-name {
    color: var(--paper);
    font-weight: 800;
    font-size: 38px;
    white-space: nowrap;
  }
</style>
</head>
<body>
  <main class="billboard">
    <div class="footer-band"></div>

    <p class="headline-lead">SHOW US YOUR</p>
    <h1 class="headline-main">
      <span class="headline-word">JUNK</span>
      <span class="headline-bang">!</span>
    </h1>

    <div class="contact">
      <svg class="camera-icon" viewBox="0 0 114 86" aria-hidden="true">
        <rect x="4" y="10" width="106" height="72" rx="12" fill="var(--camera-body)" stroke="var(--ink)" stroke-width="4"/>
        <path d="M4 36 V22 a12 12 0 0 1 12-12 h82 a12 12 0 0 1 12 12 V36 Z" fill="var(--camera-top)" stroke="var(--ink)" stroke-width="4"/>
        <rect x="70" y="2" width="26" height="10" rx="3" fill="var(--camera-top)" stroke="var(--ink)" stroke-width="4"/>
        <circle cx="52" cy="46" r="26" fill="var(--camera-top)" stroke="var(--ink)" stroke-width="4"/>
        <circle cx="52" cy="46" r="17" fill="var(--lens)" stroke="var(--ink)" stroke-width="3"/>
        <circle cx="46" cy="40" r="5" fill="#ffffff" opacity="0.7"/>
      </svg>
      <span class="phone">555-271-0836</span>
    </div>

    <div class="ribbon">
      <svg viewBox="0 0 944 68" preserveAspectRatio="none" aria-hidden="true">
        <polygon points="0,0 944,0 926,34 944,68 0,68 18,34" fill="var(--flame)"/>
      </svg>
      <span class="ribbon-text">BIG OR SMALL...WE HAUL IT ALL</span>
    </div>

    <div class="brand">
      <div class="brand-mark" aria-hidden="true"></div>
      <span class="brand-name">MEADOWLARK JUNK REMOVAL</span>
    </div>
  </main>
</body>
</html>
```